Website for Reiki and Wellness Courses

I teach online courses in Reiki and wellness/self-development and am needing a new website.

The focus of the website will be to provide descriptions of the courses as well as include a blog and pages where students in my courses will visit for additional information.

Note: courses are NOT hosted on this site.
The focus of this website will be to encourage viewers to enroll in courses as well as opt in to the email list.

I will upload copy soon. My old website is: http://brightfernstudies.example. Please do not use existing logo.

Target Market(s)

Alternative health, wellness, spirituality, personal development. Males and females of all ages seeking to improve their health and life.

Industry/Entity Type

Health And Wellness

Logo Text

No text (please do not use existing logo)

Coding

Coded - Design and coding required

Number of Pages Required

5+ page

Requirements
Must have
• 1. Home page
• 2. About page
• 3. Courses page that outlines courses (there are currently 6 courses with 1 coming soon)
• 4. Individual course page (maybe a template that I can adjust color and pictures for with each course)
• 5. Blog
• 6. Student Area that outlines all Student Areas
• 7. Individual Student Area page (maybe a template that I can adjust color and pictures for with each course)
• 8. Shop page (note: items will not currently be purchased through website - it will be a link to quillmarket for a book).
• 9. Student thank-you page (maybe a template that I can adjust color and pictures for with each course) this is the page students are directed to at end of course with vouchers for other courses.
• Opt-in for the home page, course pages, blog and thank-you pages
Nice to have
• I would like the design to be calm, clean and soothing. Ideally visitors feel relaxed when viewing the site and are encouraged to explore the courses, subscribe to the email list and purchase a product.
• ~ Testimonials page
• ~ Contact page
• I tend to gravitate towards blues, greys and purples as well as monochromatic color schemes.
Should not have
• Contact form on home page
• phone number on home page
• location/physical address
• dates for blog posts

```html
<!DOCTYPE html>
<html lang="en">
<head>
<meta charset="utf-8">
<title>Bright Fern Studies – Reiki and Wellness</title>
<link rel="stylesheet" href="https://fonts.googleapis.com/css2?family=Montserrat:wght@400;500;600&family=Open+Sans:ital,wght@0,400;0,600;1,400&display=swap">
<style>
:root{
  --slate:#6b6f94;
  --slate-dark:#5e6288;
  --blue:#4a7ab8;
  --blue-light:#5b86c0;
  --ink:#3a3d48;
  --muted:#8a8d98;
  --card-tint:#f0f0f5;
  --footer:#252833;
  --footer-base:#1f222b;
  --footer-line:#3a3e4b;
  --white:#ffffff;
}
*{box-sizing:border-box;margin:0;padding:0}
html,body{width:1200px;height:2612px;overflow:hidden}
body{position:relative;background:var(--white);font-family:"Open Sans",Arial,sans-serif;color:var(--ink)}
.abs{position:absolute}

/* top bar */
.top-bar{left:0;top:0;width:1200px;height:45px;background:var(--slate);color:#e6e7f0;font-size:11.5px}
.top-item{top:0;height:45px;display:flex;align-items:center;gap:8px}
.search{left:934px;top:8px;width:154px;height:29px;background:#7c80a3;border-radius:2px;display:flex;align-items:center;justify-content:space-between;padding:0 10px;color:#d6d8e6;font-size:11px}

/* header */
.site-header{left:0;top:45px;width:1200px;height:100px;background:var(--white)}
.brand{left:111px;top:30px;display:flex;align-items:center;gap:12px;font-family:"Montserrat",sans-serif;font-size:21px;font-weight:500;color:var(--slate)}
.brand-mark{width:40px;height:40px;border-radius:50%;background:var(--slate)}
.main-nav{left:582px;top:35px;display:flex;align-items:center;font-family:"Open Sans",sans-serif;font-size:13px;color:var(--ink)}
.main-nav a{text-decoration:none;color:inherit;height:37px;display:flex;align-items:center}
.nav-home{background:var(--blue);color:var(--white)!important;width:73px;justify-content:center}

/* hero */
.hero{left:0;top:145px;width:1200px;height:508px;background:linear-gradient(180deg,#4f5568 0%,#8a8790 28%,#c49a7a 40%,#6b6c72 52%,#4e4d52 75%,#3a3936 100%)}
.hero-title{left:108px;top:468px;font-family:"Montserrat",sans-serif;font-size:40px;font-weight:500;color:var(--white);white-space:nowrap}
.slide-arrow{width:30px;height:30px;background:rgba(0,0,0,.35);display:flex;align-items:center;justify-content:center}

/* feature cards */
.features{left:111px;top:575px;width:976px;height:374px;display:flex}
.feature{width:325.33px;height:374px;background:var(--slate);text-align:center;color:var(--white);padding-top:43px}
.feature.is-accent{background:var(--blue)}
.feature-photo{width:165px;height:165px;border-radius:50%;margin:0 auto;border:4px solid rgba(255,255,255,.85)}
.feature h3{font-family:"Montserrat",sans-serif;font-weight:500;font-size:16px;line-height:21px;margin-top:26px}
.feature p{font-size:11px;line-height:26px;margin:10px auto 0;width:290px}
.features-shadow{left:160px;top:949px;width:880px;height:40px;border-radius:50%;background:radial-gradient(ellipse at top,rgba(0,0,0,.14),rgba(0,0,0,0) 70%)}

/* welcome */
.welcome{left:0;top:1040px;width:1200px;text-align:center}
.welcome h2{font-family:"Montserrat",sans-serif;font-weight:500;font-size:33px;color:var(--ink)}
.welcome .lead{color:var(--blue);font-size:12.5px;margin-top:20px}
.welcome .body{color:var(--muted);font-size:11.5px;line-height:25px;width:840px;margin:13px auto 0}

/* opt-in */
.optin-bg{left:0;top:1273px;width:1200px;height:490px;background:linear-gradient(180deg,#5f6f76 0%,#c6b192 30%,#8c8a82 55%,#4e5158 80%,#2f3039 100%)}
.optin-box{left:111px;top:1367px;width:976px;height:312px;background:rgba(245,245,248,.9);border:3px solid var(--blue);text-align:center}
.optin-box h2{font-family:"Montserrat",sans-serif;font-weight:500;font-size:32px;color:var(--ink);margin-top:52px}
.optin-box p{font-size:11.5px;line-height:24px;color:#5b5e68;width:890px;margin:14px auto 0}
.field{top:186px;height:55px;border:1px solid #c9cbd3;background:rgba(255,255,255,.6);font-size:11.5px;color:#6a6d78;display:flex;align-items:center;padding-left:20px}
.submit{left:794px;top:186px;width:142px;height:57px;background:var(--blue);color:var(--white);font-family:"Montserrat",sans-serif;font-size:17px;font-weight:500;display:flex;align-items:center;justify-content:center}

/* testimonials */
.testimonials-title{left:0;top:1830px;width:1200px;text-align:center;font-family:"Montserrat",sans-serif;font-weight:500;font-size:31px;color:var(--ink)}
.quote-card{top:1911px;width:298px;height:160px;background:var(--card-tint);padding:28px 24px 0 36px;font-size:11px;line-height:24px;color:#7a7d88;font-style:italic}
.quote-card .mark{font-family:Georgia,serif;font-size:22px;font-style:normal;color:#8a8da0;font-weight:bold;margin-right:4px;vertical-align:-4px}
.quote-card .more{color:var(--blue);font-size:10px;font-weight:600}
.quote-name{top:2101px;font-family:"Montserrat",sans-serif;font-size:14px;color:var(--blue)}
.t-arrow{top:1981px}

/* footer */
.site-footer{left:0;top:2198px;width:1200px;height:319px;background:var(--footer);color:#e4e5ea}
.footer-col h4{font-family:"Montserrat",sans-serif;font-weight:500;font-size:20px;color:var(--white)}
.footer-col p,.footer-col li{font-size:11.5px;line-height:22px}
.footer-col ul{list-style:none;margin-top:20px}
.footer-line{top:49px;width:1px;height:236px;background:var(--footer-line)}
.contact-row{display:flex;align-items:center;gap:12px;margin-top:14px;font-size:11.5px}
.footer-base{left:0;top:2517px;width:1200px;height:95px;background:var(--footer-base);border-top:1px solid var(--footer-line);color:#e4e5ea;font-size:11.5px}
.social{top:35px;display:flex;gap:18px}
.social span{width:16px;height:16px;border-radius:50%;background:#e4e5ea;display:block}
</style>
</head>
<body>

<div class="abs top-bar">
  <div class="abs top-item" style="left:756px">
    <svg width="18" height="13" viewBox="0 0 18 13"><rect x="0.5" y="0.5" width="17" height="12" rx="1" fill="#e6e7f0"/><path d="M1 1l8 6 8-6" fill="none" stroke="#6b6f94" stroke-width="1.4"/></svg>
    <span>brightfernstudies.example</span>
  </div>
  <div class="abs search">
    <span>Search...</span>
    <svg width="11" height="11" viewBox="0 0 11 11"><circle cx="4.5" cy="4.5" r="3.5" fill="none" stroke="#e6e7f0" stroke-width="1.5"/><path d="M7 7l3.3 3.3" stroke="#e6e7f0" stroke-width="1.6"/></svg>
  </div>
</div>

<header class="abs site-header">
  <div class="abs brand"><span class="brand-mark"></span><span>Bright Fern Studies</span></div>
  <nav class="abs main-nav">
    <a class="nav-home">Home</a>
    <a style="margin-left:25px">About</a>
    <a style="margin-left:39px">Courses</a>
    <a style="margin-left:38px">Blog</a>
    <a style="margin-left:37px">Student Areas</a>
    <a style="margin-left:36px">Contact</a>
  </nav>
</header>

<section class="abs hero" role="img" aria-label="Photo of stacked stones on a beach at sunset"></section>
<div class="abs slide-arrow" style="left:37px;top:382px"><svg width="8" height="10"><path d="M6 1L2 5l4 4" fill="none" stroke="#fff" stroke-width="1.5"/></svg></div>
<div class="abs slide-arrow" style="left:1133px;top:382px"><svg width="8" height="10"><path d="M2 1l4 4-4 4" fill="none" stroke="#fff" stroke-width="1.5"/></svg></div>
<h1 class="abs hero-title">Reiki and Wellness/Self-development</h1>

<section class="abs features">
  <article class="feature">
    <div class="feature-photo" role="img" aria-label="Photo of a hands-on Reiki session" style="background:radial-gradient(circle at 50% 55%,#e6d6cc,#f4f1ef 70%)"></div>
    <h3>How Reiki Works</h3>
    <p>Reiki has been used for centuries to help individuals with physical and emotional imbalances as well as those seeking clarity and enlightenment.</p>
  </article>
  <article class="feature is-accent">
    <div class="feature-photo" role="img" aria-label="Photo of a stacked pebble tower" style="background:linear-gradient(180deg,#eef3f8 0%,#c9d6e2 55%,#9aa9b7 100%)"></div>
    <h3>Traditional Usui Reiki<br>Master Certification</h3>
    <p>Learn how to use Reiki to help yourself and others.</p>
  </article>
  <article class="feature">
    <div class="feature-photo" role="img" aria-label="Photo of smooth black stones" style="background:radial-gradient(circle at 45% 45%,#6a6a6e,#2a2a2d 75%)"></div>
    <h3>Resources</h3>
    <p>Information and tools to help you create a life you love.</p>
  </article>
</section>
<div class="abs features-shadow"></div>

<section class="abs welcome">
  <h2>Welcome To Bright Fern Studies</h2>
  <p class="lead">Thought to be centuries old and rediscovered in the late 1800's, Reiki (pronounced ray-key) is a healing and enlightenment system.</p>
  <p class="body">Reiki can be translated into "Universal (Rei) Life Energy (Ki)". As a practitioner of Reiki, you attune your awareness to this energy and utilize it for the physical and emotional healing of self and others. Reiki is non-denominational and can be practiced by everyone, regardless of their religious and spiritual beliefs. Reiki can be performed hands-on in person or from a distance.</p>
</section>

<section class="abs optin-bg" role="img" aria-label="Photo of a person with raised arms in a field at sunrise"></section>
<section class="abs optin-box">
  <h2>Stay Inspired</h2>
  <p>Receive information and articles each month to keep you feeling inspired. As a thank-you, you will also receive access to soothing music you can download for use in your Reiki sessions and meditation.</p>
  <div class="abs field" style="left:41px;width:232px">First Name</div>
  <div class="abs field" style="left:292px;width:232px">Last Name</div>
  <div class="abs field" style="left:539px;width:232px">Email Address</div>
  <div class="abs submit">Submit</div>
</section>

<h2 class="abs testimonials-title">Testimonials</h2>
<svg class="abs t-arrow" style="left:65px" width="12" height="20"><path d="M10 2L3 10l7 8" fill="none" stroke="#8a8d98" stroke-width="2.5"/></svg>
<svg class="abs t-arrow" style="left:1123px" width="12" height="20"><path d="M2 2l7 8-7 8" fill="none" stroke="#8a8d98" stroke-width="2.5"/></svg>
<div class="abs quote-card" style="left:111px"><span class="mark">&ldquo;</span>I've long been interested in Reiki, but found the costs of local workshops prohibitive. I was initially skeptical of an online Reiki class, as I am aware of the controversy... <span class="more">READ MORE</span></div>
<div class="abs quote-card" style="left:451px"><span class="mark">&ldquo;</span>I was drawn to this course with the desire to heal family, friends and pets and this course has given me that ability and more. With it, Reiki has healed me on many levels... <span class="more">READ MORE</span></div>
<div class="abs quote-card" style="left:789px"><span class="mark">&ldquo;</span>I really loved this course. The lectures were enjoyable to listen to. It was a great feature to offer them as additional downloads. The extra material like the guided... <span class="more">READ MORE</span></div>
<div class="abs quote-name" style="left:111px">Mara Lindqvist</div>
<div class="abs quote-name" style="left:451px">Owen Haldane</div>
<div class="abs quote-name" style="left:789px">Celia Marchetti</div>

<footer class="abs site-footer">
  <div class="abs footer-col" style="left:111px;top:52px;width:355px">
    <h4>About</h4>
    <p style="margin-top:28px">Thought to be centuries old and rediscovered in the late 1800's, Reiki (pronounced ray-key) is a healing and enlightenment system. reikihealingReiki can be translated into "Universal (Rei) Life Energy (Ki)". As a practitioner of Reiki, you attune your awareness to this energy and utilize it for the physical and emotional healing of self and others.</p>
  </div>
  <div class="abs footer-line" style="left:510px"></div>
  <div class="abs footer-col" style="left:580px;top:52px">
    <h4>Quick Links</h4>
    <ul style="line-height:26px"><li>About</li><li>Courses</li><li>Blog</li><li>Student Areas</li><li>Contact</li><li>Privacy Policy</li><li>Sitemap</li></ul>
  </div>
  <div class="abs footer-line" style="left:768px"></div>
  <div class="abs footer-col" style="left:840px;top:52px;width:250px">
    <h4>Contact</h4>
    <p style="margin-top:20px">Reiki is traditionally taught in 3 levels, First Degree, Second Degree and Master's Degree and all are offered online.</p>
    <div class="contact-row" style="margin-top:16px">
      <svg width="18" height="13" viewBox="0 0 18 13"><rect x="0.5" y="0.5" width="17" height="12" rx="1" fill="#e4e5ea"/><path d="M1 1l8 6 8-6" fill="none" stroke="#252833" stroke-width="1.4"/></svg>
      <span>info@brightfernstudies.example</span>
    </div>
  </div>
</footer>

<div class="abs footer-base">
  <div class="abs" style="left:111px;top:37px">Copyright &copy; 2016 Bright Fern Studies.&nbsp; All Right Reserved.</div>
  <div class="abs social" style="left:968px" aria-label="Social links"><span></span><span></span><span></span><span></span></div>
</div>

</body>
</html>
```